Push notification screens at app start up

We have an existing news publication app platform and are adding categories to push notifications.

We need two screens designed (each for Zorbel, Quillet and Android for a total of 6d) that show when the app is first launched.

The workflow of our app:
0. app launch screen while webservices run (no work needed)
1. information screen to the user promoting the benefits of push notification with "Next" button. (see concept attached)
2. Push categories selection screen. This will have list of category types, with on/off switch.

"Select the categories that you wish to receive occasional notices:
Breaking News (on/off switch)
Local News (on/off switch)
Sports (on/off switch)
Local Events (on/off switch)
Weather Alerts (on/off switch)
Local Deals (on/off switch)"

"Enable these categories on the next screen."
"Next" button

Background:
When I was looking around at app designs, I came across this one (http://www.plinthworks.example/design/7719034) and I really liked it. We obviously have different features on our screen, but I’d like to have this same feel. The colors used in this design are perfect.

UPDATE: I do not mean to limit your design to match the layout as the one mentioned above. Please use your creativity for the layout.

Our standard font in Helvetica Neue.

Notes:
- our app is developed for all phone devices from Zorbel 4 to Zorbel 6, so designs should be thoughtful of vertical scrolling if needed.
- our app is developed for Quillets, so we'll need designs completed as well. (We can finalize Zorbel design first, then translate the design to Quillet.)
- our app is developed for Android phones (not tablets), so we'll need designs completed as well. (We can finalize iOS design first, then translater to Android UI design guidelines).

We hope to establish a good on-going relationship with the designer for as-needed work in the future.

News

• Helvetica Neue

• Clean designs. No clutter.
• We would likely go with the standard on/off switches for both iOS and Android, but are open to small custom variations.

```html
<!DOCTYPE html>
<html lang="en">
<head>
<meta charset="utf-8">
<title>Push Notice Categories</title>
<link rel="stylesheet" href="https://fonts.googleapis.com/css2?family=Roboto:wght@400;500;700&display=swap">
<style>
  :root {
    --brand-blue: #3a98dc;
    --subtitle-blue: #3b9ad9;
    --label-grey: #555a5f;
    --icon-grey: #8a8d90;
    --divider: #e3e4e6;
    --track-off: #e2e2e2;
    --surface: #ffffff;
    --on-brand: #ffffff;
  }
  * { box-sizing: border-box; margin: 0; padding: 0; }
  html, body {
    width: 675px; height: 1200px; overflow: hidden;
    background: var(--surface);
    font-family: "Roboto", "Helvetica Neue", Arial, sans-serif;
  }
  .screen { position: relative; width: 675px; height: 1200px; background: var(--surface); }

  .top-band { background: var(--brand-blue); color: var(--on-brand); height: 150px; }

  .status-bar {
    height: 45px; display: flex; align-items: center; justify-content: space-between;
    padding: 0 14px; font-size: 24px; font-weight: 500; position: relative;
  }
  .status-left, .status-right { display: flex; align-items: center; gap: 8px; }
  .signal { display: flex; gap: 3px; }
  .signal span { width: 11px; height: 11px; border-radius: 50%; border: 1.5px solid var(--on-brand); }
  .signal span.full { background: var(--on-brand); }
  .status-time { position: absolute; left: 0; right: 0; text-align: center; pointer-events: none; }
  .battery { width: 50px; height: 20px; border: 2px solid var(--on-brand); border-radius: 4px; padding: 2px; position: relative; }
  .battery::after { content: ""; position: absolute; right: -6px; top: 5px; width: 3px; height: 7px; background: var(--on-brand); border-radius: 0 2px 2px 0; }
  .battery-level { width: 100%; height: 100%; background: var(--on-brand); border-radius: 1px; }

  .header-notice {
    text-align: center; font-size: 27px; font-weight: 700; line-height: 34px;
    padding-top: 17px;
  }

  .prompt {
    text-align: center; color: var(--subtitle-blue); font-size: 26.5px; line-height: 34px;
    padding-top: 40px; height: 149px;
  }

  .category-list { list-style: none; border-top: 2px solid var(--divider); }
  .category {
    height: 100px; display: flex; align-items: center; border-bottom: 2px solid var(--divider);
    padding: 0 15px 0 34px;
  }
  .category-icon { width: 30px; height: 27px; flex: none; }
  .category-label { margin-left: 37px; flex: 1; color: var(--label-grey); font-size: 28px; font-weight: 700; }

  .switch {
    width: 92px; height: 52px; border-radius: 26px; background: var(--surface);
    border: 2.5px solid var(--track-off); position: relative; flex: none;
  }
  .switch-knob {
    position: absolute; top: 0; left: 0; width: 47px; height: 47px; border-radius: 50%;
    background: var(--surface); box-shadow: 0 2px 5px rgba(0,0,0,0.25);
  }
  .switch.is-on { background: var(--brand-blue); border-color: var(--brand-blue); }
  .switch.is-on .switch-knob { left: auto; right: 0; }
</style>
</head>
<body>
<div class="screen">
  <header class="top-band">
    <div class="status-bar">
      <div class="status-left">
        <div class="signal"><span class="full"></span><span class="full"></span><span class="full"></span><span></span><span></span></div>
        <span class="carrier">TELVA</span>
        <svg width="24" height="18" viewBox="0 0 24 18" aria-hidden="true">
          <path d="M12 17 L2 6 A15 15 0 0 1 22 6 Z" fill="#fff"/>
        </svg>
      </div>
      <div class="status-time">4:21 PM</div>
      <div class="status-right">
        <span>100%</span>
        <div class="battery"><div class="battery-level"></div></div>
      </div>
    </div>
    <p class="header-notice">You must enable Push Notices on<br>the next screen to apply these settings.</p>
  </header>

  <p class="prompt">Select the categories of notices you<br>wish to receive:</p>

  <ul class="category-list">
    <li class="category">
      <svg class="category-icon" viewBox="0 0 30 27" aria-hidden="true"><rect x="1" y="1" width="28" height="25" fill="none" stroke="#8a8d90" stroke-width="2"/><rect x="5" y="6" width="8" height="7" fill="#8a8d90"/><path d="M16 7h9M16 11h9M5 16h20M5 20h20" stroke="#8a8d90" stroke-width="2"/></svg>
      <span class="category-label">Breaking News</span>
      <span class="switch"><span class="switch-knob"></span></span>
    </li>
    <li class="category">
      <svg class="category-icon" viewBox="0 0 30 27" aria-hidden="true"><rect x="1" y="1" width="28" height="25" fill="none" stroke="#8a8d90" stroke-width="2"/><rect x="5" y="6" width="8" height="7" fill="#8a8d90"/><path d="M16 7h9M16 11h9M5 16h20M5 20h20" stroke="#8a8d90" stroke-width="2"/></svg>
      <span class="category-label">Local News</span>
      <span class="switch is-on"><span class="switch-knob"></span></span>
    </li>
    <li class="category">
      <svg class="category-icon" viewBox="0 0 30 27" aria-hidden="true"><rect x="1" y="1" width="28" height="25" fill="none" stroke="#8a8d90" stroke-width="2"/><rect x="5" y="6" width="8" height="7" fill="#8a8d90"/><path d="M16 7h9M16 11h9M5 16h20M5 20h20" stroke="#8a8d90" stroke-width="2"/></svg>
      <span class="category-label">Sports</span>
      <span class="switch"><span class="switch-knob"></span></span>
    </li>
    <li class="category">
      <svg class="category-icon" viewBox="0 0 30 27" aria-hidden="true"><rect x="1" y="1" width="28" height="25" fill="none" stroke="#8a8d90" stroke-width="2"/><rect x="5" y="6" width="8" height="7" fill="#8a8d90"/><path d="M16 7h9M16 11h9M5 16h20M5 20h20" stroke="#8a8d90" stroke-width="2"/></svg>
      <span class="category-label">Local Events</span>
      <span class="switch"><span class="switch-knob"></span></span>
    </li>
    <li class="category">
      <svg class="category-icon" viewBox="0 0 30 27" aria-hidden="true"><rect x="1" y="1" width="28" height="25" fill="none" stroke="#8a8d90" stroke-width="2"/><rect x="5" y="6" width="8" height="7" fill="#8a8d90"/><path d="M16 7h9M16 11h9M5 16h20M5 20h20" stroke="#8a8d90" stroke-width="2"/></svg>
      <span class="category-label">Weather Alerts</span>
      <span class="switch"><span class="switch-knob"></span></span>
    </li>
    <li class="category">
      <svg class="category-icon" viewBox="0 0 30 27" aria-hidden="true"><rect x="1" y="1" width="28" height="25" fill="none" stroke="#8a8d90" stroke-width="2"/><rect x="5" y="6" width="8" height="7" fill="#8a8d90"/><path d="M16 7h9M16 11h9M5 16h20M5 20h20" stroke="#8a8d90" stroke-width="2"/></svg>
      <span class="category-label">Local Deals</span>
      <span class="switch"><span class="switch-knob"></span></span>
    </li>
  </ul>
</div>
</body>
</html>
```